Business Card Design Project

restaurant management company needs business card design.

Industry/Entity Type

Restaurant

Requirements
Must have
• our logo
bramble den logo
QLW logo
WrapNest Logo
Nice to have
• Morley Quint
(position)

238 Halvey Street
Brennick Falls QV,
Estmoor
E3K 2R8

Tel 555-xxx-xxxx Ext 348
Fax 555-xxx-xxxx
Mobile 555-xxx-xxxx

morleyquint@kbrholdings.example
Should not have
• Morley Quint
(position)

238 Halvey Street
Brennick Falls QV,
Estmoor
E3K 2R8

Tel 555-xxx-xxxx Ext 348
Fax 555-xxx-xxxx
Mobile 555-xxx-xxxx

morleyquint@kbrholdings.example

```html
<!DOCTYPE html>
<html lang="en">
<head>
<meta charset="utf-8">
<title>Morley Quint – Business Card</title>
<link rel="stylesheet" href="https://fonts.googleapis.com/css2?family=Open+Sans:wght@400;600;700&display=swap">
<style>
  :root {
    --brand-red: #ee1c25;
    --card-white: #ffffff;
    --backdrop: #e4e1dc;
    --text-white: #ffffff;
  }
  * { margin: 0; padding: 0; box-sizing: border-box; }
  html, body {
    width: 1200px;
    height: 900px;
    overflow: hidden;
    background: var(--backdrop);
    font-family: "Open Sans", Arial, sans-serif;
  }
  .business-card {
    position: absolute;
    left: 74px;
    top: 146px;
    width: 1052px;
    height: 608px;
    background: var(--card-white);
    overflow: hidden;
  }
  .header-band {
    position: absolute;
    left: 0;
    top: 0;
    width: 1052px;
    height: 608px;
  }
  .header-band path { fill: var(--brand-red); }
  .holder {
    position: absolute;
    left: 46px;
    top: 94px;
    color: var(--text-white);
  }
  .holder-name {
    font-size: 36px;
    font-weight: 700;
    letter-spacing: 0.5px;
    line-height: 1.2;
  }
  .holder-position {
    font-size: 29px;
    font-weight: 400;
    line-height: 1.3;
  }
  .company-mark {
    position: absolute;
    right: 56px;
    top: 70px;
    color: var(--text-white);
    font-weight: 400;
    text-align: right;
  }
  .company-mark .mark-name {
    display: block;
    font-size: 100px;
    line-height: 0.9;
    letter-spacing: 2px;
  }
  .company-mark .mark-full {
    display: block;
    font-size: 13px;
    margin-top: 12px;
  }
  .contact {
    position: absolute;
    left: 46px;
    color: var(--brand-red);
    font-size: 26px;
    font-weight: 600;
    line-height: 34px;
    font-style: normal;
  }
  .contact-address { top: 346px; }
  .contact-phones { top: 430px; }
  .contact-email { top: 548px; }
  .brand-partner {
    position: absolute;
    top: 458px;
    color: var(--brand-red);
    font-size: 22px;
    font-weight: 700;
    line-height: 32px;
    transform: translateX(-50%);
    white-space: nowrap;
  }
  .partner-qlw { left: 652px; }
  .partner-bramble { left: 800px; }
  .partner-wrapnest { left: 954px; }
</style>
</head>
<body>
  <main class="business-card">
    <svg class="header-band" viewBox="0 0 1052 608" aria-hidden="true">
      <path d="M0 0 H1052 V196 Q540 430 0 222 Z"/>
    </svg>

    <header class="holder">
      <h1 class="holder-name">MORLEY QUINT</h1>
      <p class="holder-position">(position)</p>
    </header>

    <div class="company-mark">
      <span class="mark-name">ZELQ</span>
      <span class="mark-full">Zelquin Restaurant Holdings Inc</span>
    </div>

    <address class="contact contact-address">
      238 Halvey Street, Brennick Falls, QV<br>
      Estmoor, E3K 2R8
    </address>

    <p class="contact contact-phones">
      Phone 555-xxx-xxxx Ext 348<br>
      Fax 555-xxx-xxxx<br>
      Mobile 555-xxx-xxxx
    </p>

    <p class="contact contact-email">morleyquint@kbrholdings.example</p>

    <span class="brand-partner partner-qlw">QLW</span>
    <span class="brand-partner partner-bramble">bramble den</span>
    <span class="brand-partner partner-wrapnest">WrapNest</span>
  </main>
</body>
</html>
```